Business Card Design

My business is writing crime novels to entertain readers. I write legal thrillers and mysteries. I need a card for publishers, agents, other authors, and media.

Industry/Entity Type

Legal

Contact Information for Business Card

Paul Derrow
www.derrowfiction.example
pauljderrow@inkpost.example
0064 27 5190472

```html
<!DOCTYPE html>
<html lang="en">
<head>
<meta charset="utf-8">
<title>Paul Derrow — Business Card</title>
<link rel="stylesheet" href="https://fonts.googleapis.com/css2?family=Libre+Baskerville:wght@700&family=Open+Sans:wght@400&display=swap">
<style>
  :root {
    --page-bg: #e6e7ea;
    --slate: #454c58;
    --slate-deep: #3b414c;
    --card-light: #f4f4f5;
    --card-shade: #e3e4e6;
    --ink: #3c424e;
    --rule: #d9dbde;
    --photo-top: #8d8e90;
    --photo-bottom: #5f6062;
  }
  * { margin: 0; padding: 0; box-sizing: border-box; }
  html, body {
    width: 1200px;
    height: 864px;
    overflow: hidden;
    background: var(--page-bg);
  }
  .stage {
    width: 1200px;
    height: 864px;
    display: flex;
    align-items: center;
    justify-content: center;
  }
  .business-card {
    position: relative;
    width: 900px;
    height: 514px;
    display: flex;
    background: linear-gradient(180deg, var(--card-light) 0%, var(--card-shade) 100%);
    box-shadow: 0 18px 40px rgba(40, 44, 52, 0.22);
  }
  .portrait-panel {
    width: 336px;
    height: 100%;
    background: linear-gradient(180deg, var(--slate) 0%, var(--slate-deep) 100%);
    display: flex;
    align-items: center;
    justify-content: center;
    border-right: 3px solid var(--rule);
    box-shadow: 6px 0 0 var(--card-light), 8px 0 0 var(--rule);
  }
  .portrait-frame {
    width: 208px;
    height: 208px;
    border: 2px solid #dfe1e4;
    background: linear-gradient(180deg, var(--photo-top) 0%, var(--photo-bottom) 100%);
  }
  .details-panel {
    flex: 1;
    position: relative;
    padding: 78px 0 0 76px;
  }
  .holder-name {
    font-family: "Libre Baskerville", "Times New Roman", serif;
    font-weight: 700;
    font-size: 29px;
    letter-spacing: 0.5px;
    color: var(--ink);
    text-transform: uppercase;
  }
  .contact-list {
    position: absolute;
    left: 76px;
    bottom: 62px;
    list-style: none;
  }
  .contact-item {
    display: flex;
    align-items: center;
    gap: 18px;
    height: 38px;
    font-family: "Open Sans", Arial, sans-serif;
    font-size: 20px;
    letter-spacing: 1.2px;
    color: var(--ink);
  }
  .contact-icon {
    width: 22px;
    height: 22px;
    flex: none;
  }
</style>
</head>
<body>
<main class="stage">
  <article class="business-card">
    <section class="portrait-panel">
      <div class="portrait-frame" role="img" aria-label="Portrait photograph of Paul Derrow"></div>
    </section>
    <section class="details-panel">
      <h1 class="holder-name">Paul Derrow</h1>
      <ul class="contact-list">
        <li class="contact-item">
          <svg class="contact-icon" viewBox="0 0 22 22" aria-hidden="true">
            <rect x="6" y="2" width="10" height="18" rx="1.5" fill="none" stroke="#3c424e" stroke-width="1.6"/>
            <line x1="9.5" y1="17" x2="12.5" y2="17" stroke="#3c424e" stroke-width="1.4"/>
          </svg>
          <span>0064 27 5190472</span>
        </li>
        <li class="contact-item">
          <svg class="contact-icon" viewBox="0 0 22 22" aria-hidden="true">
            <rect x="2" y="4" width="18" height="12" rx="1" fill="none" stroke="#3c424e" stroke-width="1.6"/>
            <line x1="11" y1="16" x2="11" y2="19" stroke="#3c424e" stroke-width="1.6"/>
            <line x1="7" y1="19.5" x2="15" y2="19.5" stroke="#3c424e" stroke-width="1.6"/>
          </svg>
          <span>www.derrowfiction.example</span>
        </li>
        <li class="contact-item">
          <svg class="contact-icon" viewBox="0 0 22 22" aria-hidden="true">
            <rect x="2" y="5" width="18" height="12" fill="#3c424e"/>
            <polyline points="2,5 11,12 20,5" fill="none" stroke="#f4f4f5" stroke-width="1.4"/>
          </svg>
          <span>pauljderrow@inkpost.example</span>
        </li>
      </ul>
    </section>
  </article>
</main>
</body>
</html>
```